Corinnehabbard.com

1. Conceptualization and designing of the site Homepage. The Homepage design will be completely customized and based on your design instructions (i.e. preferred colors, links to reference sites that you want us to take reference from if any etc) and the recently completed logo design.
2. Upon homepage design approval, based on it we will be creating the layout for the other 4 site inner pages (i.e. About page, Contact page, Services page, and Insights (publications, media).
3. Once all the inner page designs are approved, we will get the designs built (will make sure that the site is completely Responsive - works on all devices) within your provided WIX account.
4. We will add the static text and images provided by you to the Home page, About page, Contact page, and the Services page. For the 2 Insights sub-pages, we will add 1-2 sample Publications and Media entries.
once you confirm the total number of required entries for the 2 sub-pages, I will accordingly quote you on the same
5. Integration of a Contact form on the Contact page that will email the filled in details to your mail id.

```html
<!DOCTYPE html>
<html lang="en">
<head>
<meta charset="utf-8">
<title>Corinne Habbard Consulting</title>
<link href="https://fonts.googleapis.com/css2?family=Josefin+Sans:wght@600;700&family=Roboto:wght@400;500;700&display=swap" rel="stylesheet">
<style>
:root{
  --green:#128a3e;
  --green-band:#0f8c45;
  --blue:#0a9be3;
  --red:#e0101c;
  --orange:#f29a10;
  --ink:#111;
  --body:#555;
  --grey-bg:#f3f3f3;
  --field:#efefef;
  --line:#d9d9d9;
}
*{box-sizing:border-box;margin:0;padding:0}
html,body{width:1200px;height:3258px;overflow:hidden;background:#fff}
body{font-family:'Roboto',sans-serif;color:var(--ink)}
.page{position:relative;width:1200px;height:3258px;overflow:hidden}
.abs{position:absolute}
.display{font-family:'Josefin Sans',sans-serif;font-weight:700;letter-spacing:.5px}

/* top bar */
.topbar{left:0;top:0;width:1200px;height:28px;background:var(--green);color:#fff;font-size:11.5px}
.topbar span{position:absolute;top:8px}
.dot{display:inline-block;width:8px;height:8px;border-radius:50%;background:#fff;margin-right:5px;vertical-align:-1px}

/* nav */
.nav{left:0;top:28px;width:1200px;height:71px;background:#fff}
.nav a{position:absolute;top:29px;font-size:14.5px;font-weight:500;color:var(--ink);text-decoration:none}
.logo-tab{left:516px;top:28px;width:167px;height:97px;background:#fff;clip-path:polygon(0 0,100% 0,100% 74%,88% 100%,12% 100%,0 74%);z-index:3}
.brand-circle{position:absolute;left:61px;top:12px;width:44px;height:44px;border-radius:50%;border:2px solid #222}
.brand-name{position:absolute;left:0;top:60px;width:167px;text-align:center;font-family:'Roboto',sans-serif;font-weight:700;font-size:10px;line-height:11px;color:var(--blue);letter-spacing:.4px}
.btn{position:absolute;display:flex;align-items:center;justify-content:center;gap:10px;background:var(--blue);color:#fff;border-radius:30px;font-weight:700;font-size:15px;text-decoration:none}
.btn svg{width:24px;height:10px}

/* hero */
.hero-photo{left:0;top:99px;width:1200px;height:600px;background:linear-gradient(90deg,#d8dde0 0%,#c9ccc8 35%,#9a9791 55%,#c8c4bf 72%,#e2e4e6 100%)}
.hero-title{left:144px;top:226px;font-size:46px;line-height:60px}
.hero-title .g{color:var(--green)}
.hero-copy{left:144px;top:350px;width:390px;font-size:16.5px;line-height:26px;color:#111}

/* about */
.about-ring{left:138px;top:760px;width:424px;height:424px;border-radius:50%;border-left:6px solid #111;border-bottom:6px solid #111}
.about-photo{left:148px;top:762px;width:418px;height:418px;border-radius:50%;background:radial-gradient(circle at 45% 45%,#b69a84 0%,#8c8f93 50%,#d5d7d9 100%)}
.about-title{left:636px;top:812px;font-size:34px}
.about-copy{left:636px;top:872px;width:419px;font-size:13.8px;line-height:24.8px;color:var(--body);text-align:justify}
.about-copy p+p{margin-top:9px}

/* services */
.grey{left:0;top:1240px;width:1200px;height:822px;background:var(--grey-bg)}
.section-title{left:0;width:1200px;text-align:center;font-size:34px}
.svc-photo{width:298px;height:298px;border-radius:50%}
.svc-icon{width:80px;height:80px;border-radius:50%;border:3px solid #fff}
.svc-name{width:440px;text-align:center;font-weight:700;font-size:17.5px}
.svc-copy{width:440px;text-align:center;font-size:13.5px;line-height:19.5px;color:var(--body)}

/* consultation band */
.band{left:0;top:2061px;width:1200px;height:316px;background:var(--green-band);color:#fff}
.band-title{left:0;top:2134px;width:1200px;text-align:center;font-size:31px;font-weight:600;color:#fff}
.band-copy{left:180px;top:2192px;width:840px;text-align:center;font-size:14px;line-height:23px;color:#fff}
.call{left:467px;top:2263px;width:268px;height:45px;border-radius:30px;background:var(--blue);color:#fff;font-weight:700;font-size:14px}
.call-disc{position:absolute;left:4px;top:3px;width:39px;height:39px;border-radius:50%;background:#fff}

/* contact */
.field{position:absolute;background:var(--field);border:1px solid var(--line);border-radius:26px;font-size:13px;color:#888;padding:16px 26px}
.message{border-radius:24px}

/* footer */
.footer-text{color:#fff}
.f-head{font-weight:700;font-size:17px;color:#fff}
.f-links{left:529px;top:3024px;list-style:none;font-size:13.5px;line-height:25px;color:#fff}
.sub-box{left:786px;top:3031px;width:267px;height:41px;border-radius:22px;background:#fff;border:2px solid var(--blue)}
.sub-btn{position:absolute;right:1px;top:1px;width:96px;height:35px;border-radius:20px;background:var(--blue);color:#fff;font-weight:700;font-size:14px;display:flex;align-items:center;justify-content:center}
.soc{width:30px;height:30px;border-radius:50%;border:1.5px solid #fff}
</style>
</head>
<body>
<div class="page">

  <!-- top bar -->
  <div class="abs topbar">
    <span style="left:143px"><i class="dot"></i>info@corinnehabbard.com</span>
    <span style="left:515px">
      <svg width="8" height="11" viewBox="0 0 8 11" style="vertical-align:-1px"><path d="M4 0a4 4 0 0 1 4 4c0 3-4 7-4 7S0 7 0 4a4 4 0 0 1 4-4z" fill="#fff"/></svg>
      952 Lorem ipsum dolor sit amet</span>
    <span style="left:872px"><i class="dot" style="margin-right:8px"></i><i class="dot" style="margin-right:8px"></i><i class="dot"></i> |</span>
    <span style="left:956px">
      <svg width="10" height="10" viewBox="0 0 10 10" style="vertical-align:-1px"><path d="M2 0l2 2.5-1.2 1.2c.6 1.4 1.6 2.4 3 3L7 5.5 10 7.5 9 10C4 10 0 6 0 1z" fill="#fff"/></svg>
      +1-888-888-8888</span>
  </div>

  <!-- hero photo -->
  <div class="abs hero-photo" role="img" aria-label="Two business professionals reviewing a tablet in a bright office"></div>
  <svg class="abs" style="left:0;top:560px" width="1200" height="140" viewBox="0 0 1200 140" aria-hidden="true">
    <path d="M0 20 Q 320 130 640 112 Q 950 98 1200 14 L1200 140 L0 140 Z" fill="#fff"/>
    <path d="M240 108 Q 640 150 1200 14 L1200 40 Q 640 165 240 108 Z" fill="var(--red)"/>
  </svg>

  <!-- nav -->
  <div class="abs nav">
    <a style="left:143px">Home</a>
    <a style="left:253px">About Us</a>
    <a style="left:388px">Insights
      <svg width="9" height="6" viewBox="0 0 9 6" style="margin-left:4px;vertical-align:2px"><path d="M1 1l3.5 3.5L8 1" stroke="#111" stroke-width="1.4" fill="none"/></svg></a>
    <a style="left:727px">Services</a>
    <a style="left:851px">Contact us</a>
    <a class="btn" style="left:959px;top:18px;width:96px;height:36px;font-size:14.5px;gap:6px">
      <svg width="10" height="12" viewBox="0 0 10 12" style="width:10px;height:12px"><rect x="0" y="5" width="10" height="7" rx="1" fill="#fff"/><path d="M2.5 5V3.5a2.5 2.5 0 0 1 5 0V5" stroke="#fff" stroke-width="1.6" fill="none"/></svg>Login</a>
  </div>
  <div class="abs logo-tab">
    <div class="brand-circle"></div>
    <div class="brand-name">CORINNE HABBARD<br>CONSULTING</div>
  </div>

  <!-- hero text -->
  <h1 class="abs display hero-title">CORINNE HABBARD<br><span class="g">CONSULTING</span></h1>
  <p class="abs hero-copy">Lorem ipsum dolor sit amet, consectetur adipiscing elit, sed do eiusmod tempor incididunt ut.</p>
  <a class="btn" style="left:144px;top:425px;width:166px;height:49px;font-size:16px">Get Started
    <svg viewBox="0 0 24 10"><path d="M0 5h22M17 1l5 4-5 4" stroke="#fff" stroke-width="1.6" fill="none"/></svg></a>

  <!-- about -->
  <div class="abs about-ring"></div>
  <div class="abs about-photo" role="img" aria-label="Colleagues talking together around a meeting table"></div>
  <h2 class="abs display about-title">ABOUT US</h2>
  <div class="abs about-copy">
    <p>Lorem ipsum dolor sit amet, consectetur adipiscing elit, sed do eiusmod tempor incididunt ut labore et dolore magna aliqua. Ut enim ad minim veniam, quis nostrud exercitation ullamco.</p>
    <p>Duis aute irure dolor in reprehenderit in voluptate velit esse cillum dolore eu fugiat nulla pariatur. Excepteur sint occaecat cupidatat non proident, sunt in culpa qui officia deserunt mollit anim id est laborum."ullamco laboris nisi ut aliquip ex ea commodo.</p>
  </div>
  <a class="btn" style="left:636px;top:1080px;width:157px;height:44px;font-size:14.5px">Learn More
    <svg viewBox="0 0 24 10"><path d="M0 5h22M17 1l5 4-5 4" stroke="#fff" stroke-width="1.6" fill="none"/></svg></a>

  <!-- services -->
  <div class="abs grey"></div>
  <svg class="abs" style="left:0;top:1215px" width="1200" height="80" viewBox="0 0 1200 80" aria-hidden="true">
    <path d="M0 5 Q 230 40 460 75 Q 640 80 860 30 Q 1030 0 1200 30 L1200 80 L0 80 Z" fill="var(--grey-bg)"/>
    <path d="M0 5 Q 160 25 300 55 Q 430 80 560 75 L0 80 Z" fill="var(--grey-bg)"/>
  </svg>
  <h2 class="abs display section-title" style="top:1358px">OUR SERVICES</h2>

  <div class="abs svc-photo" style="left:211px;top:1467px;background:linear-gradient(135deg,#c9a58e,#6f7379 55%,#d0d2d4)" role="img" aria-label="Business people shaking hands"></div>
  <div class="abs" style="left:211px;top:1467px;width:298px;height:298px;border-radius:50%;border:5px solid var(--red);border-top-color:transparent;transform:rotate(-20deg)"></div>
  <div class="abs svc-icon" style="left:320px;top:1724px;background:var(--red)" role="img" aria-label="Consulting icon"></div>
  <div class="abs svc-name" style="left:140px;top:1822px">CONSULTING</div>
  <p class="abs svc-copy" style="left:140px;top:1853px">Lorem ipsum dolor sit amet, consectetur adipiscing elit, sed do eiusmod tempor incididunt ut labore et dolore magna aliqua. Ut enim ad minim veniam, quis nostrud exercitation.</p>
  <a class="btn" style="left:274px;top:1938px;width:156px;height:45px;font-size:14.5px">Learn More
    <svg viewBox="0 0 24 10"><path d="M0 5h22M17 1l5 4-5 4" stroke="#fff" stroke-width="1.6" fill="none"/></svg></a>

  <div class="abs svc-photo" style="left:707px;top:1467px;background:linear-gradient(135deg,#e8e6e3,#c9a88f 45%,#2b6fc4 80%)" role="img" aria-label="Smiling registered nurse in blue scrubs"></div>
  <div class="abs" style="left:707px;top:1467px;width:298px;height:298px;border-radius:50%;border:5px solid var(--orange);border-top-color:transparent;transform:rotate(-20deg)"></div>
  <div class="abs svc-icon" style="left:816px;top:1724px;background:var(--orange)" role="img" aria-label="Nurse icon"></div>
  <div class="abs svc-name" style="left:636px;top:1822px">TRAINING OF REGISTERED NURSES</div>
  <p class="abs svc-copy" style="left:636px;top:1853px">Lorem ipsum dolor sit amet, consectetur adipiscing elit, sed do eiusmod tempor incididunt ut labore et dolore magna aliqua. Ut enim ad minim veniam, quis nostrud exercitation.</p>
  <a class="btn" style="left:770px;top:1938px;width:156px;height:45px;font-size:14.5px">Learn More
    <svg viewBox="0 0 24 10"><path d="M0 5h22M17 1l5 4-5 4" stroke="#fff" stroke-width="1.6" fill="none"/></svg></a>

  <!-- consultation band -->
  <div class="abs band"></div>
  <h2 class="abs display band-title">CONTACT US FOR A FREE&nbsp; CONSULTATION</h2>
  <p class="abs band-copy">Lorem ipsum dolor sit amet, consectetur adipiscing elit, sed do eiusmod tempor incididunt ut labore et dolore magna aliqua,Ut enim ad minim veniam, quis nostrud exercitation ullamco laboris nisi ut aliquip ex ea commodo consequat.</p>
  <a class="btn call abs">
    <span class="call-disc"></span>
    <svg width="16" height="16" viewBox="0 0 10 10" style="position:absolute;left:15px;top:14px;width:16px;height:16px"><path d="M2 0l2 2.5-1.2 1.2c.6 1.4 1.6 2.4 3 3L7 5.5 10 7.5 9 10C4 10 0 6 0 1z" fill="var(--blue)"/></svg>
    <span style="margin-left:34px">CALL US +1-888-888-8888</span></a>

  <!-- contact form -->
  <h2 class="abs display section-title" style="top:2452px">CONTACT US</h2>
  <div class="field" style="left:221px;top:2532px;width:367px;height:48px">Name</div>
  <div class="field" style="left:225px;top:2596px;width:367px;height:48px">Email Address</div>
  <div class="field" style="left:225px;top:2657px;width:367px;height:48px">Phone Number</div>
  <div class="field message" style="left:609px;top:2532px;width:370px;height:173px">Message</div>
  <a class="btn" style="left:513px;top:2749px;width:174px;height:45px;font-size:14.5px">Submit Now
    <svg viewBox="0 0 24 10"><path d="M0 5h22M17 1l5 4-5 4" stroke="#fff" stroke-width="1.6" fill="none"/></svg></a>

  <!-- footer -->
  <svg class="abs" style="left:0;top:2860px" width="1200" height="398" viewBox="0 0 1200 398" aria-hidden="true">
    <path d="M0 140 Q 420 0 860 30 Q 1060 55 1200 140 L1200 398 L0 398 Z" fill="#000"/>
    <path d="M0 125 Q 400 -5 880 20 Q 560 20 0 150 Z" fill="var(--orange)"/>
  </svg>
  <div class="abs" style="left:222px;top:2990px;width:92px;height:92px;border-radius:50%;border:2px solid #fff"></div>
  <div class="abs" style="left:143px;top:3094px;width:250px;text-align:center;font-weight:700;font-size:20px;line-height:22px;color:var(--blue);letter-spacing:.5px">CORINNE HABBARD<br>CONSULTING</div>

  <div class="abs f-head" style="left:529px;top:2983px">QUICK LINKS</div>
  <ul class="abs f-links">
    <li>Home</li><li>About Us</li><li>Services</li><li>Insights</li><li>Contact Us</li>
  </ul>

  <div class="abs f-head" style="left:785px;top:2983px">SUBSCRIBE TO OUR EMAIL</div>
  <div class="abs sub-box">
    <span style="position:absolute;left:20px;top:12px;font-size:11px;color:#777">Emaill Address</span>
    <span class="sub-btn">Submit</span>
  </div>
  <div class="abs footer-text" style="left:784px;top:3099px;font-size:11px;font-weight:500">
    <svg width="11" height="11" viewBox="0 0 11 11" style="vertical-align:-1px;margin-right:6px"><rect x=".5" y=".5" width="10" height="10" rx="1.5" stroke="#fff" fill="none"/><path d="M2.5 5.5l2 2 4-4" stroke="#fff" stroke-width="1.4" fill="none"/></svg>Are you interested in follow to a particular website</div>
  <div class="abs soc" style="left:783px;top:3134px" role="img" aria-label="Social profile"></div>
  <div class="abs soc" style="left:822px;top:3134px" role="img" aria-label="Social profile"></div>
  <div class="abs soc" style="left:861px;top:3134px" role="img" aria-label="Social profile"></div>

  <div class="abs" style="left:143px;top:3193px;width:912px;height:1px;background:#333"></div>
  <div class="abs footer-text" style="left:143px;top:3218px;font-size:13px">Copyright © 2024 Corinne Habbard Consulting - All Rights Reserved.</div>
  <div class="abs footer-text" style="left:827px;top:3218px;font-size:13px">Terms and Conditions &nbsp;&nbsp;| &nbsp;&nbsp;Privacy Policy</div>

</div>
</body>
</html>
```